Sierra Lantern Roots Festival Music Conference & Concert Series needs a banner design to welco...

We are looking for a banner to use as a backdrop where people can take pictures and promote the event as they upload to social media. The music conference primarily targets high school students so we are looking for a design that will attract a younger audience. The festival revolves around music appreciation in the US/Mexico border. We like the "Sierra LanternRoots Festival" trumpet logo on the "5th annual" design attached, but we are open to other designs.
Target Market(s)
ages 15-45
Colors
Designer to choose colors to be used in the design.
Look and feel

```html
<!DOCTYPE html>
<html lang="en">
<head>
<meta charset="utf-8">
<title>Sierra Lantern Roots Festival – Music Conference &amp; Concert Series</title>
<link rel="stylesheet" href="https://fonts.googleapis.com/css2?family=Jost:wght@400;500&display=swap">
<style>
  :root {
    --bg-left: #4a6fb0;
    --bg-mid: #5a3f8a;
    --bg-right: #a3407f;
    --layer-outer: rgba(70, 40, 70, 0.75);
    --layer-mid: rgba(45, 35, 75, 0.85);
    --panel: #262626;
    --neon-cyan: #72f1f7;
    --neon-pink: #f26af0;
    --neon-gold: #e8b422;
    --frame-orange: #f0925a;
    --frame-purple: #7a45c0;
    --frame-rose: #e06a8a;
    --text-white: #ffffff;
  }
  * { margin: 0; padding: 0; box-sizing: border-box; }
  html, body { width: 1200px; height: 960px; overflow: hidden; background: var(--panel); }
  .banner {
    position: relative; width: 1200px; height: 960px; overflow: hidden;
    background: linear-gradient(100deg, var(--bg-left) 0%, var(--bg-mid) 40%, var(--bg-right) 100%);
    font-family: "Jost", "Futura", sans-serif;
  }
  .layer-svg { position: absolute; inset: 0; width: 1200px; height: 960px; }

  .art-slot { position: absolute; }
  .art-slot--guitar { background: radial-gradient(ellipse at center, rgba(100,205,240,.55) 0%, rgba(100,205,240,.25) 45%, rgba(100,205,240,0) 72%); }
  .art-slot--guitar-top { left: 234px; top: -30px; width: 290px; height: 110px; }
  .art-slot--guitar-left { left: -20px; top: 700px; width: 180px; height: 280px; }
  .art-slot--guitar-right { left: 830px; top: 875px; width: 290px; height: 120px; }
  .art-slot--hat { background: radial-gradient(ellipse at center, rgba(232,180,34,.6) 0%, rgba(232,180,34,.28) 45%, rgba(232,180,34,0) 72%); }
  .art-slot--hat-right { left: 980px; top: 212px; width: 180px; height: 124px; transform: rotate(-25deg); }
  .art-slot--hat-left { left: 358px; top: 696px; width: 196px; height: 130px; transform: rotate(28deg); }

  .edition {
    position: absolute; left: 720px; width: 148px; top: 272px; text-align: right;
    font-size: 22px; font-weight: 400; color: var(--text-white); letter-spacing: .3px; line-height: 1;
  }
  .name-halo {
    position: absolute; left: 300px; top: 330px; width: 584px; height: 80px; border-radius: 40px;
    background: radial-gradient(ellipse at center, rgba(114,241,247,.28), rgba(114,241,247,0) 70%);
  }
  .event-name { font-weight: 400; }
  .event-name__main {
    position: absolute; left: 0; top: 318px; width: 1200px; text-align: center;
    font-size: 72px; line-height: 100px; color: var(--neon-cyan); font-weight: 400;
  }
  .event-name__sub {
    position: absolute; left: 0; top: 440px; width: 1200px; text-align: center;
    font-size: 62px; line-height: 70px; color: var(--neon-pink); font-weight: 400;
    text-shadow: 0 0 8px rgba(242,106,240,.8), 0 0 20px rgba(242,106,240,.5);
  }
  .tagline {
    position: absolute; left: 0; top: 524px; width: 1200px; text-align: center;
    font-size: 24px; font-weight: 500; color: var(--text-white); letter-spacing: 2.6px; line-height: 32px;
    text-shadow: 0 0 8px rgba(255,255,255,.55);
  }
</style>
</head>
<body>
<main class="banner">
  <svg class="layer-svg" viewBox="0 0 1200 960" aria-hidden="true">
    <path fill="var(--layer-outer)" d="M60 95 L190 32 L420 88 L620 40 L1000 42 L1170 110 L1185 420 L1125 580 L1160 720 L1155 860 L1040 940 L600 905 L330 950 L110 880 L60 700 L95 520 L30 300 Z"/>
    <path fill="var(--layer-mid)" d="M95 110 L270 80 L440 140 L620 95 L820 85 L1010 95 L1120 170 L1150 330 L1100 560 L1130 750 L1110 870 L900 900 L600 860 L330 900 L120 850 L100 640 L140 420 L90 260 Z"/>
    <path fill="var(--panel)" d="M130 118 L310 92 L445 132 L600 97 L785 163 L940 118 L1060 128 L1100 200 L1080 420 L1060 520 L1088 640 L1070 820 L1010 840 L800 830 L600 870 L380 830 L200 875 L110 830 L100 700 L125 560 L105 420 L100 230 Z"/>
  </svg>

  <div class="art-slot art-slot--guitar art-slot--guitar-top" role="img" aria-label="Neon outline guitar"></div>
  <div class="art-slot art-slot--guitar art-slot--guitar-left" role="img" aria-label="Neon outline guitar"></div>
  <div class="art-slot art-slot--guitar art-slot--guitar-right" role="img" aria-label="Neon outline guitar"></div>
  <div class="art-slot art-slot--hat art-slot--hat-right" role="img" aria-label="Neon outline sombrero"></div>
  <div class="art-slot art-slot--hat art-slot--hat-left" role="img" aria-label="Neon outline sombrero"></div>

  <svg class="layer-svg" viewBox="0 0 1200 960" aria-hidden="true">
    <defs>
      <linearGradient id="frameGradient" x1="0" y1="0" x2="1" y2="0">
        <stop offset="0" stop-color="var(--frame-orange)"/>
        <stop offset="0.3" stop-color="#c0509a"/>
        <stop offset="0.6" stop-color="var(--frame-purple)"/>
        <stop offset="1" stop-color="var(--frame-rose)"/>
      </linearGradient>
      <filter id="frameGlow" x="-10%" y="-30%" width="120%" height="160%">
        <feGaussianBlur stdDeviation="3" result="b"/>
        <feMerge><feMergeNode in="b"/><feMergeNode in="SourceGraphic"/></feMerge>
      </filter>
      <symbol id="sparkle" viewBox="-1 -1 2 2" overflow="visible">
        <g stroke="#fff" stroke-width="0.09" fill="none">
          <line x1="0" y1="-0.4" x2="0" y2="-1"/><line x1="0" y1="0.4" x2="0" y2="1"/>
          <line x1="-0.4" y1="0" x2="-1" y2="0"/><line x1="0.4" y1="0" x2="1" y2="0"/>
          <line x1="0.3" y1="-0.3" x2="0.7" y2="-0.7"/><line x1="-0.3" y1="-0.3" x2="-0.7" y2="-0.7"/>
          <line x1="0.3" y1="0.3" x2="0.7" y2="0.7"/><line x1="-0.3" y1="0.3" x2="-0.7" y2="0.7"/>
        </g>
      </symbol>
    </defs>

    <g class="title-frame" fill="none" stroke="url(#frameGradient)" stroke-width="5" filter="url(#frameGlow)">
      <polyline points="351,313 351,302 866,302 866,330"/>
      <polyline points="351,412 351,430 866,430 866,418"/>
    </g>

    <g class="sparkles">
      <use href="#sparkle" x="67" y="324" width="62" height="62"/>
      <use href="#sparkle" x="546" y="126" width="40" height="40"/>
      <use href="#sparkle" x="997" y="72" width="70" height="70"/>
      <use href="#sparkle" x="131" y="584" width="40" height="40"/>
      <use href="#sparkle" x="247" y="822" width="40" height="40"/>
      <use href="#sparkle" x="1050" y="744" width="66" height="66"/>
    </g>

    <g class="shooting-stars" fill="none" stroke="#fff" stroke-width="2.2">
      <circle cx="190" cy="157" r="13"/>
      <line x1="169" y1="147" x2="136" y2="114"/>
      <line x1="177" y1="136" x2="164" y2="123"/>
      <line x1="196" y1="136" x2="183" y2="125"/>

      <circle cx="1041" cy="577" r="9"/>
      <line x1="1055" y1="587" x2="1078" y2="606"/>
      <line x1="1050" y1="596" x2="1060" y2="604"/>
      <line x1="1037" y1="590" x2="1045" y2="598"/>

      <circle cx="709" cy="750" r="13"/>
      <line x1="700" y1="763" x2="671" y2="801"/>
      <line x1="721" y1="765" x2="711" y2="780"/>
      <line x1="703" y1="770" x2="694" y2="785"/>
    </g>
  </svg>

  <p class="edition">6TH ANNUAL</p>
  <div class="name-halo" aria-hidden="true"></div>
  <h1 class="event-name">
    <span class="event-name__main">Sierra LanternRoots</span>
    <span class="event-name__sub">Festival</span>
  </h1>
  <p class="tagline">MUSIC CONFERENCE &amp; CONCERT SERIES</p>
</main>
</body>
</html>
```